Trendy eye catching business card for lawn mowing business

Turf Tidy, a local community lawn mowing service, requires an eye catching trendy business card to drop into letterboxes.

We could simply throw something together from a Microsoft Word template, but we are wanting something more than this. Some other business’ images are attached for some inspiration.

We are requiring the card to have Turf Tidy with our slogan, Call The Brindles. In addition, provide details with that we are a local, affordable lawn mowing service, and for other gardening matters to simply just ask!
Plus the relevant contact details, phone, email, social media.

Target Market(s)

Local community members who require assistance with their garden care

Industry/Entity Type

Gardening

Contact Information for Business Card

the name TURF TIDY is our logo
telephone logo 0438 215 967
email logo turftidy@postbox-mail.example
Instagram logo turftidy
Facebook logo turftidy.sth
Lawn Mowing Service
Local Affordable
edge trim, blow and clipping removal included.
Other gardening matters, just ask!

Font styles to use
Serif
Sans Serif
Decorative
Script

Colors
9bcb3c
ffffff

Requirements
Must have
• All the details listed in Business Card Details.
Make these words prominent:
Turf Tidy
Lawn Mowing Service
Local
Affordable
Nice to have
• Our slogan ‘Call The Brindles’ incorporated.
Different colour background for front and reverse side
Greens, white and black colours
Subtle grass blades images incorporated
Should not have
• No images of lawnmowers.
No images of men/cartoons.
No using initials for Turf Tidy

```html
<!DOCTYPE html>
<html lang="en">
<head>
<meta charset="utf-8">
<title>Turf Tidy – Business Card</title>
<link rel="stylesheet" href="https://fonts.googleapis.com/css2?family=Roboto:wght@400;700;900&family=Orbitron:wght@400&display=swap">
<style>
  :root {
    --green: #86c043;
    --green-soft: rgba(134,192,67,.18);
    --ink: #1c1c1c;
    --card-dark: #222222;
    --white: #ffffff;
    --grey: #8a8a8a;
    --grey-light: #bdbdbd;
    --slogan-grey: #5a5a5a;
    --page: #d9d9d9;
  }
  * { margin: 0; padding: 0; box-sizing: border-box; }
  html, body { width: 1200px; height: 801px; overflow: hidden; }
  body {
    background: var(--page);
    font-family: "Roboto", Arial, sans-serif;
    position: relative;
  }
  .card {
    position: absolute;
    top: 274px;
    width: 443px;
    height: 263px;
    overflow: hidden;
    box-shadow: 0 2px 5px rgba(0,0,0,.35);
  }
  .card--front { left: 152px; background: var(--white); }
  .card--back { left: 625px; background: var(--card-dark); color: var(--white); }

  /* shared slogan with rules either side */
  .slogan {
    position: absolute;
    display: flex; align-items: center; gap: 6px;
    font-weight: 700; text-transform: uppercase; white-space: nowrap;
  }
  .slogan::before, .slogan::after {
    content: ""; display: block; height: 1px; background: currentColor; flex: 1;
  }

  /* front */
  .front-logo {
    position: absolute; left: 28px; top: 40px;
    font-weight: 900; font-size: 46px; line-height: 1;
    letter-spacing: -0.5px; color: var(--green); white-space: nowrap;
  }
  .card--front .slogan {
    left: 28px; top: 85px; width: 263px;
    font-size: 16px; letter-spacing: 2.2px; color: var(--slogan-grey);
  }
  .contact-list { position: absolute; left: 28px; list-style: none; }
  .contact-list--direct { top: 151px; }
  .contact-list--social { top: 208px; }
  .contact-list li {
    display: flex; align-items: center; gap: 6px;
    font-size: 13px; line-height: 16px; height: 16px; color: var(--ink);
    white-space: nowrap;
  }
  .contact-icon { width: 14px; height: 14px; flex: none; }
  .social-dot {
    width: 13px; height: 13px; border-radius: 50%;
    border: 1.5px solid var(--grey); flex: none;
  }
  .grass-front {
    position: absolute; left: 300px; top: 14px; width: 130px; height: 240px;
    background: linear-gradient(to top, var(--green-soft), rgba(134,192,67,0));
  }
  .front-band {
    position: absolute; left: 0; bottom: 0; width: 100%; height: 9px; background: var(--green);
  }

  /* back */
  .back-block { position: absolute; left: 0; width: 100%; text-align: center; white-space: nowrap; }
  .service-title { top: 45px; font-weight: 700; font-size: 22px; letter-spacing: .3px; }
  .service-tagline { top: 72px; font-size: 19px; color: var(--green); }
  .service-details { top: 107px; font-size: 14.5px; line-height: 18px; }
  .back-phone {
    top: 146px; font-family: "Orbitron", Arial, sans-serif;
    font-size: 18px; letter-spacing: 1.5px; color: var(--green);
  }
  .back-logo {
    top: 196px; font-weight: 700; font-size: 29px; line-height: 1;
    letter-spacing: .5px; color: var(--white);
  }
  .card--back .slogan {
    left: 100px; top: 228px; width: 243px;
    font-size: 12px; letter-spacing: 2px; color: var(--grey-light);
  }
  .grass-back {
    position: absolute; top: 128px; width: 88px; height: 135px;
    background: linear-gradient(to top, rgba(134,192,67,.3), rgba(134,192,67,0));
  }
  .grass-back--left { left: 0; }
  .grass-back--right { left: 355px; }
</style>
</head>
<body>

<section class="card card--front" aria-label="Business card front">
  <div class="grass-front" role="img" aria-label="Tall green grass blades illustration"></div>

  <div class="front-logo">TURF TIDY</div>
  <div class="slogan">Call The Brindles</div>

  <ul class="contact-list contact-list--direct">
    <li>
      <svg class="contact-icon" viewBox="0 0 14 14" aria-hidden="true">
        <rect x="0.75" y="0.75" width="12.5" height="12.5" rx="1.5" fill="none" stroke="#86c043" stroke-width="1.5"/>
        <path d="M4 3.2c.4-.3.8-.2 1 .2l.7 1.3c.2.4 0 .7-.3.9l-.4.3c.4 1 1.2 1.8 2.2 2.2l.3-.4c.2-.3.6-.4.9-.2l1.3.7c.4.2.5.6.2 1l-.6.7c-.4.4-1 .5-1.6.3C5.6 9.6 4.3 8.3 3.6 6.2c-.2-.6-.1-1.2.3-1.6z" fill="#86c043"/>
      </svg>
      0438 215 967
    </li>
    <li>
      <svg class="contact-icon" viewBox="0 0 14 14" aria-hidden="true">
        <rect x="0" y="2.5" width="14" height="9.5" fill="#86c043"/>
        <path d="M0 2.5 7 8l7-5.5" fill="none" stroke="#fff" stroke-width="1.2"/>
      </svg>
      turftidy@postbox-mail.example
    </li>
  </ul>

  <ul class="contact-list contact-list--social">
    <li><span class="social-dot" aria-hidden="true"></span>instagram.com/turftidy</li>
    <li><span class="social-dot" aria-hidden="true"></span>fb.me/turftidy.sth</li>
  </ul>

  <div class="front-band"></div>
</section>

<section class="card card--back" aria-label="Business card back">
  <div class="grass-back grass-back--left" role="img" aria-label="Green grass blades illustration"></div>
  <div class="grass-back grass-back--right" role="img" aria-label="Green grass blades illustration"></div>

  <h1 class="back-block service-title">LAWN MOWING SERVICE</h1>
  <p class="back-block service-tagline">Local. Affordable.</p>
  <p class="back-block service-details">Edge trim, blow and clipping removal included.<br>Other gardening matters, just ask!</p>
  <p class="back-block back-phone">0438 215 967</p>
  <div class="back-block back-logo">TURF TIDY</div>
  <div class="slogan">Call The Brindles</div>
</section>

</body>
</html>
```